Business Card & Email Signature Design || Upmarket + Luxury

Rima Vale Honey, a New Zealand Manuka Honey company needs a Business Card & Email Signature design.

Our logo's are attached in Gold & Black versions, feel free to be creative with how you use the logo and it's patterns in your design.

Style:
- Looking for an Elegant, Luxurious, Upmarket feel.
- Black/Matte Black Card, Gold Foil, UV Embossing

Information to Add:

- Logo
- Company Name: Rima Vale Honey
- Name: Martin Holloway
- Title: Creative Director
- Phone: +64 2815 96 417
- Email: martin@rimavalehoney.example.nz
- Website: www.rimavalehoney.example.nz

- Socials: ***For email Signature Only***
- Facebook: https://www.facebook.com/rimavalehoney/
- Instagram: https://www.instagram.com/rimavalehoney/

Target Market(s)

Asia/Europe Luxury, Upmarket

Contact Information for Business Card

- Logo
- Name: Martin Holloway
- Phone: +64 2815 96 417

Font styles to use
Other font styles liked:
• Champagne & Limousines (Attached)

Requirements
Must have
• Business Card & Email Signature Design.

Looking for a Sleek, Luxury, Upmarket Design.

```html
<!DOCTYPE html>
<html lang="en">
<head>
<meta charset="utf-8">
<title>Rima Vale Honey – Business Card</title>
<link rel="stylesheet" href="https://fonts.googleapis.com/css2?family=Montserrat:wght@300;400;600&display=swap">
<style>
  :root {
    --backdrop: #a3a3a3;
    --card: #1d1d1d;
    --gold: #c9a14c;
    --gold-light: #e0c27a;
  }
  * { margin: 0; padding: 0; box-sizing: border-box; }
  html, body {
    width: 1200px; height: 1199px; overflow: hidden;
    background: var(--backdrop);
    font-family: "Montserrat", sans-serif;
  }
  .card {
    position: absolute; left: 195px; width: 800px; height: 435px;
    background: var(--card);
  }
  .card--front { top: 115px; }
  .card--back { top: 650px; }

  .brand-block {
    position: absolute; left: 230px; top: 140px; width: 340px;
    transform: translateX(-50%); text-align: center;
  }
  .brand-mark {
    display: block; margin: 0 auto 26px;
    width: 78px; height: 78px; border-radius: 50%;
    border: 1.5px solid var(--gold);
  }
  .brand-name {
    color: var(--gold); font-weight: 300; font-size: 22px;
    letter-spacing: 4px; text-transform: uppercase; white-space: nowrap;
  }

  .divider {
    position: absolute; left: 386px; top: 146px;
    width: 2px; height: 147px; background: var(--gold);
  }

  .contact { position: absolute; left: 434px; top: 140px; color: var(--gold); }
  .contact__name {
    font-weight: 600; font-size: 28px; letter-spacing: 1.5px;
    text-transform: uppercase; color: var(--gold-light); line-height: 1.1;
    white-space: nowrap;
  }
  .contact__title { font-weight: 400; font-size: 19px; margin-top: 4px; letter-spacing: .5px; }
  .contact__list { list-style: none; margin-top: 18px; }
  .contact__item {
    display: flex; align-items: center; gap: 8px;
    font-size: 16px; line-height: 27px; white-space: nowrap; letter-spacing: .3px;
  }
  .contact__icon { width: 13px; height: 13px; flex: none; }

  .seal {
    position: absolute; left: 253px; top: 69px;
    width: 294px; height: 294px; border-radius: 50%;
    border: 1.5px solid var(--gold);
    display: flex; align-items: center; justify-content: center;
  }
  .seal .brand-name { font-size: 21px; }
</style>
</head>
<body>
  <section class="card card--front">
    <div class="brand-block">
      <span class="brand-mark"></span>
      <p class="brand-name">Rima Vale Honey</p>
    </div>
    <div class="divider"></div>
    <div class="contact">
      <h1 class="contact__name">Martin Holloway</h1>
      <p class="contact__title">Creative Director</p>
      <ul class="contact__list">
        <li class="contact__item">
          <svg class="contact__icon" viewBox="0 0 16 16"><path d="M4 1l3 3-2 2c1 2 3 4 5 5l2-2 3 3-2 3C7 15 1 9 1 3z" fill="none" stroke="currentColor" stroke-width="1.4"/></svg>
          +64 2815 96 417
        </li>
        <li class="contact__item">
          <svg class="contact__icon" viewBox="0 0 16 16"><rect x="1" y="3.5" width="14" height="9" fill="none" stroke="currentColor" stroke-width="1.4"/><path d="M1 4l7 5 7-5" fill="none" stroke="currentColor" stroke-width="1.4"/></svg>
          martin@rimavalehoney.example.nz
        </li>
        <li class="contact__item">
          <svg class="contact__icon" viewBox="0 0 16 16"><circle cx="8" cy="8" r="6.5" fill="none" stroke="currentColor" stroke-width="1.3"/><ellipse cx="8" cy="8" rx="2.8" ry="6.5" fill="none" stroke="currentColor" stroke-width="1.1"/><path d="M1.5 8h13M2.5 5h11M2.5 11h11" stroke="currentColor" stroke-width="1"/></svg>
          www.rimavalehoney.example.nz
        </li>
      </ul>
    </div>
  </section>

  <section class="card card--back">
    <div class="seal">
      <p class="brand-name">Rima Vale Honey</p>
    </div>
  </section>
</body>
</html>
```